Bright Towns Forum PowerPoint Design Template and Sample Deck

The Bright Towns Forum is an international organization that seeks to improve the livability, workability and sustainability of the world’s cities.
We seek a versatile PowerPoint design template with 10 slide types plus a “self-documenting” sample deck. Your design will be used in keynote speeches and workshops around the world.
After the contest is completed, we will ask the winning designer to add 10-20 additional slide types for $75 per slide. We also seek a long-term relationship whereby we can request “custom” slides and/or ask the designer to touch up the slides we build to make them better.
FILES. We have uploaded several files:
2. PALETTE. Shows our official colors.
3 LOGOS. Several individual files with different variations of our logo. Some with our motto, some without.
2. SAMPLE SLIDES. Because we were unable to successfully upload our sample deck, we are making it available via this FileNook link:
https://www.filenook-example.com/s/k7qrtmzp2wd9hxa/The%20Bright%20Towns%20Forum%20Design%20Contest%20Notes.docx?dl=0
Target Market(s)
Mayors, department heads, CIOs, senior executives from technology companies
Industry/Entity Type
Information Technology
Colors
Designer to choose colors to be used in the design.
Requirements
Must have
- Please see uploaded Word document for requirements, nice to haves and should not haves and uploaded palette for color preferences.
Nice to have
- see above
Should not have
- see above

```html
<!DOCTYPE html>
<html lang="en">
<head>
<meta charset="utf-8">
<title>Bright Towns Forum – Slide Samples</title>
<link href="https://fonts.googleapis.com/css2?family=Carlito:ital,wght@0,400;0,700;1,400&display=swap" rel="stylesheet">
<style>
  :root {
    --page-bg: #ffffff;
    --sky-blue: #2c5d9d;
    --sky-blue-light: #3b6aa8;
    --sky-blue-dark: #1f4c88;
    --strip-navy: #0f3564;
    --deep-navy: #032d5a;
    --accent-orange: #f7941d;
    --text-white: #ffffff;
    --pin-blue: #3a6fc4;
    --pin-green: #7a9a1a;
    --map-tone: #e9eef5;
  }
  html, body {
    margin: 0;
    padding: 0;
    width: 1200px;
    height: 1200px;
    overflow: hidden;
    background: var(--page-bg);
    font-family: "Carlito", "Calibri", sans-serif;
  }
  .canvas {
    position: relative;
    width: 1200px;
    height: 1200px;
  }
  .slide {
    position: absolute;
    overflow: hidden;
    color: var(--text-white);
  }
  /* Title slide */
  .slide--title {
    left: 187px;
    top: 95px;
    width: 828px;
    height: 465px;
  }
  .skyline-photo {
    position: absolute;
    inset: 0 0 10px 0;
    background: linear-gradient(180deg, var(--sky-blue-light) 0%, var(--sky-blue) 45%, var(--sky-blue-dark) 100%);
  }
  .bottom-strip {
    position: absolute;
    left: 0; right: 0; bottom: 0;
    height: 10px;
    background: var(--strip-navy);
  }
  .headline {
    position: absolute;
    left: 0; right: 0;
    top: 118px;
    margin: 0;
    text-align: center;
    font-size: 56px;
    line-height: 68px;
    font-weight: 700;
    letter-spacing: 0.2px;
  }
  .headline .accent { color: var(--accent-orange); }
  .quote {
    position: absolute;
    left: 0; right: 0;
    top: 256px;
    margin: 0;
    padding: 0;
    text-align: center;
    font-size: 21px;
    line-height: 26px;
  }
  .quote p { margin: 0; }
  .quote cite {
    display: block;
    font-style: italic;
  }
  /* Map slide */
  .slide--map {
    left: 185px;
    top: 645px;
    width: 830px;
    height: 467px;
    background: var(--deep-navy);
  }
  .slide-title {
    position: absolute;
    left: 0; right: 0;
    top: 13px;
    margin: 0;
    text-align: center;
    font-size: 30px;
    line-height: 40px;
    font-weight: 700;
  }
  .title-dots {
    position: absolute;
    left: 394px;
    top: 63px;
    display: flex;
    gap: 2px;
  }
  .title-dots span {
    width: 6px;
    height: 6px;
    background: var(--text-white);
  }
  .world-map {
    position: absolute;
    left: 10px;
    top: 103px;
    width: 569px;
    height: 324px;
    background: var(--map-tone);
    border-radius: 18px;
  }
  .map-pin {
    position: absolute;
    width: 15px;
    height: 15px;
    margin: -7.5px 0 0 -7.5px;
    border-radius: 50%;
    background: var(--pin-blue);
  }
  .map-pin::after {
    content: "";
    position: absolute;
    left: 4px; top: 4px;
    width: 5px; height: 5px;
    border: 1px solid var(--text-white);
    border-radius: 50%;
  }
  .map-pin--highlight { background: var(--pin-green); }
  .side-copy {
    position: absolute;
    left: 602px;
    top: 170px;
    width: 196px;
    font-size: 10px;
    font-style: italic;
    line-height: 19px;
  }
  .side-copy p { margin: 0 0 18px; }
</style>
</head>
<body>
<div class="canvas">

  <section class="slide slide--title">
    <div class="skyline-photo" role="img" aria-label="City skyline of high-rise towers under a cloudy sky, tinted blue"></div>
    <div class="bottom-strip"></div>
    <h1 class="headline">The world is <span class="accent">changing</span></h1>
    <blockquote class="quote">
      <p>“The biggest shift in economic gravity in history.”</p>
      <cite>Harlow &amp; Penn Advisory</cite>
    </blockquote>
  </section>

  <section class="slide slide--map">
    <h2 class="slide-title">Your Slide Title Here</h2>
    <div class="title-dots"><span></span><span></span><span></span><span></span><span></span></div>
    <div class="world-map" role="img" aria-label="White world map silhouette showing all continents"></div>
    <span class="map-pin" style="left:125px; top:201px;"></span>
    <span class="map-pin" style="left:313px; top:279px;"></span>
    <span class="map-pin" style="left:433px; top:249px;"></span>
    <span class="map-pin" style="left:489px; top:356px;"></span>
    <span class="map-pin map-pin--highlight" style="left:181px; top:345px;"></span>
    <div class="side-copy">
      <p>Lorem Ipsum is simply dummy text of the printing and typesetting industry.</p>
      <p>Lorem Ipsum has been the industry's standard dummy text ever since the 1500s, when an unknown printer took a galley of type and scrambled it to make a type specimen book.</p>
      <p>It has survived not only five centuries, but also the leap into electronic typesetting, remaining essentially unchanged.</p>
    </div>
  </section>

</div>
</body>
</html>
```